Business Card Design

We provide services doing multiple jobs in the construction industry.Please note: The company name needs to be ROCK SOLID BUILDING SERVICESAttached logo was an example of what we wanted. Can you change up the colors?

Industry/Entity Type

Construction

Contact Information for Business Card

ROCK SOLID BUILDING SERVICES5401 HUDSON BEND RDAUSTIN, TX 78734(512)243-6854ROCKSOLIDBUILDINGSERVICES@GMAIL.COM

```html
<!DOCTYPE html>
<html lang="en">
<head>
<meta charset="utf-8">
<title>Pearlwood Framing Works — Business Card</title>
<link rel="stylesheet" href="https://fonts.googleapis.com/css2?family=Michroma&display=swap">
<style>
  :root {
    --page: #e9e9eb;
    --card: #f7f7f8;
    --navy: #232060;
    --slate: #9a9ca3;
    --ink: #3a3a40;
    --rule: #8c8d93;
    --mark: #2b2a6e;
  }
  html, body {
    margin: 0;
    width: 1200px;
    height: 900px;
    overflow: hidden;
    background: var(--page);
  }
  .canvas {
    position: relative;
    width: 1200px;
    height: 900px;
    font-family: "Michroma", sans-serif;
  }
  .card {
    position: absolute;
    left: 285px;
    width: 630px;
    height: 360px;
    background: var(--card);
    border-radius: 28px;
    overflow: hidden;
    box-shadow: 0 6px 18px rgba(0,0,0,0.12);
  }
  .card--front { top: 60px; }
  .card--back  { top: 480px; }

  .swoosh { position: absolute; inset: 0; width: 630px; height: 360px; }

  .brand {
    position: absolute;
    display: flex;
    align-items: center;
    gap: 10px;
    color: var(--mark);
    letter-spacing: 0.5px;
    white-space: nowrap;
  }
  .brand__dot {
    width: 14px; height: 14px;
    border-radius: 50%;
    background: var(--mark);
    flex: none;
  }
  .card--front .brand { left: 230px; top: 82px; font-size: 14px; }
  .card--back .brand { left: 50%; top: 50%; transform: translate(-50%, -50%); font-size: 20px; }

  .contact {
    position: absolute;
    top: 168px;
    font-size: 8.5px;
    letter-spacing: 0.3px;
    color: var(--ink);
    line-height: 15px;
    white-space: nowrap;
  }
  .contact--person { right: 375px; text-align: right; }
  .contact__name { font-size: 9.5px; color: #222; }
  .divider {
    position: absolute;
    left: 267px; top: 168px;
    width: 1px; height: 75px;
    background: var(--rule);
  }
  .contact--lines { left: 278px; }
  .contact__row { display: flex; align-items: center; gap: 6px; }
  .icon { width: 9px; height: 9px; flex: none; }
</style>
</head>
<body>
<div class="canvas">

  <section class="card card--front">
    <svg class="swoosh" viewBox="0 0 630 360" aria-hidden="true">
      <path d="M0 225 C120 235 250 290 345 360 L0 360 Z" fill="var(--slate)"/>
      <path d="M0 250 C110 262 215 310 300 360 L0 360 Z" fill="#ffffff"/>
      <path d="M0 258 C100 272 195 318 265 360 L0 360 Z" fill="var(--navy)"/>
      <path d="M0 330 C40 338 70 348 85 360 L0 360 Z" fill="#d9dadd"/>
    </svg>

    <div class="brand"><span class="brand__dot"></span>PEARLWOOD FRAMING WORKS</div>

    <div class="contact contact--person">
      <div class="contact__name">DANA WHITLOW</div>
      <div>OWNER / C.E.O</div>
      <div>7732 FERNGLEN PASS LN</div>
      <div>AUSTIN, TX 78734</div>
    </div>

    <div class="divider"></div>

    <div class="contact contact--lines">
      <div class="contact__row">
        <svg class="icon" viewBox="0 0 12 12"><circle cx="6" cy="6" r="6" fill="var(--ink)"/><path d="M4 3 L5 5 L4.5 6 Q5.5 7.5 6 7.5 L7 7 L9 8 Q8.5 9.5 7.5 9.5 Q3 8.5 2.5 4.5 Q2.5 3.3 4 3Z" fill="#fff"/></svg>
        (512)555-0193
      </div>
      <div class="contact__row">
        <svg class="icon" viewBox="0 0 12 12"><circle cx="6" cy="6" r="6" fill="var(--ink)"/><rect x="4" y="2.5" width="4" height="7" rx="1" fill="#fff"/></svg>
        (512)555-0147
      </div>
      <div class="contact__row">
        <svg class="icon" viewBox="0 0 12 12"><circle cx="6" cy="6" r="6" fill="var(--ink)"/><rect x="3" y="4" width="6" height="4" fill="#fff"/></svg>
        (512)555-0162
      </div>
      <div class="contact__row">
        <svg class="icon" viewBox="0 0 12 12"><circle cx="6" cy="6" r="6" fill="var(--ink)"/><rect x="3" y="4" width="6" height="4.2" fill="#fff"/><path d="M3 4 L6 6.5 L9 4" stroke="var(--ink)" stroke-width="0.8" fill="none"/></svg>
        PEARLWOODFRAMINGWORKS@MAILNEST.EXAMPLE
      </div>
      <div class="contact__row">
        <svg class="icon" viewBox="0 0 12 12"><circle cx="6" cy="6" r="6" fill="var(--ink)"/><circle cx="6" cy="6" r="3.5" fill="none" stroke="#fff" stroke-width="0.9"/><path d="M2.5 6 H9.5 M6 2.5 V9.5" stroke="#fff" stroke-width="0.8"/></svg>
        WWW.PEARLWOODFRAMING.EXAMPLE
      </div>
    </div>
  </section>

  <section class="card card--back">
    <div class="brand"><span class="brand__dot"></span>PEARLWOOD FRAMING WORKS</div>
  </section>

</div>
</body>
</html>
```